New Business Card Design Project

Need a design that will create an impact / strong impression towards our clients for our business. We are in the lighting business and we do lighting retrofits for large commercial to industrial clientele.

Target Market(s)

Lighting Industry

Industry/Entity Type

Business

Font styles to use
Other font styles liked:
• we would like to use the font on our logo, not sure what it is though..

Requirements
Must have
• Our logo.
Nice to have
• We are open to suggestions that have to do with lighting.

```html
<!DOCTYPE html>
<html lang="en">
<head>
<meta charset="utf-8">
<title>Beacon Upgrade Works – Business Card</title>
<link rel="stylesheet" href="https://fonts.googleapis.com/css2?family=Source+Sans+3:wght@400;600;700&display=swap">
<style>
  :root {
    --backdrop: #2b2b2b;
    --green-bright: #12c258;
    --green-deep: #08843a;
    --green-dark: #1d5a2c;
    --green-mid: #3c9a3f;
    --ink: #4a4a4a;
    --rule: #8c8c8c;
    --paper: #ffffff;
  }
  * { margin: 0; padding: 0; box-sizing: border-box; }
  html, body {
    width: 1200px; height: 900px; overflow: hidden;
    background: var(--backdrop);
    font-family: "Source Sans 3", "Myriad Pro", sans-serif;
  }
  .canvas {
    width: 1200px; height: 900px;
    display: flex; flex-direction: column;
    align-items: center; justify-content: center; gap: 56px;
  }
  .card {
    position: relative;
    width: 640px; height: 366px;
    box-shadow: 0 10px 30px rgba(0,0,0,.45);
    overflow: hidden;
  }

  /* Front */
  .card--front {
    background: linear-gradient(110deg, var(--green-bright) 0%, var(--green-deep) 75%);
    color: var(--paper);
  }
  .brand {
    display: flex; align-items: center; gap: 12px;
    font-weight: 700; letter-spacing: .04em; text-transform: uppercase;
  }
  .brand__square { width: 16px; height: 16px; background: currentColor; flex: none; }
  .card--front .brand {
    position: absolute; left: 0; right: 0; top: 140px;
    justify-content: center; font-size: 30px;
  }
  .card--front .brand-rule {
    position: absolute; left: 150px; right: 150px; top: 190px;
    height: 1px; background: rgba(255,255,255,.85);
  }
  .card--front .website {
    position: absolute; left: 0; right: 0; top: 240px;
    text-align: center; font-size: 15px; letter-spacing: .22em;
  }

  /* Back */
  .card--back { background: var(--paper); color: var(--ink); }
  .edge-tab {
    position: absolute; left: 0; top: 96px;
    width: 10px; height: 40px; background: var(--green-dark);
  }
  .person { position: absolute; left: 34px; top: 96px; line-height: 1.1; }
  .person__name { font-weight: 700; font-size: 19px; color: var(--green-dark); text-transform: uppercase; }
  .person__title { font-weight: 400; font-size: 17px; color: var(--green-mid); text-transform: uppercase; }
  .card--back .brand {
    position: absolute; right: 34px; top: 92px;
    color: var(--green-dark); font-size: 22px; gap: 9px;
  }
  .card--back .brand__square { width: 12px; height: 12px; }
  .rule {
    position: absolute; height: 1px; background: var(--rule);
  }
  .rule--upper { left: 200px; right: 34px; top: 138px; }
  .rule--lower { left: 200px; width: 200px; top: 262px; }
  .address {
    position: absolute; right: 34px; top: 154px;
    text-align: right; font-size: 16px; line-height: 1.25;
  }
  .contacts {
    position: absolute; left: 200px; top: 272px;
    list-style: none; font-size: 16px; line-height: 1.2;
  }
  .contacts li { display: flex; align-items: center; gap: 9px; }
  .contacts svg { width: 12px; height: 12px; fill: var(--ink); flex: none; }
</style>
</head>
<body>
<main class="canvas">

  <section class="card card--front" aria-label="Business card front">
    <div class="brand"><span class="brand__square"></span><span>Beacon Upgrade Works, LLC</span></div>
    <div class="brand-rule"></div>
    <p class="website">www.beaconupgradeworks.com</p>
  </section>

  <section class="card card--back" aria-label="Business card back">
    <div class="edge-tab"></div>
    <div class="person">
      <p class="person__name">Daniel Reyes</p>
      <p class="person__title">CEO/Founder</p>
    </div>

    <div class="brand"><span class="brand__square"></span><span>Beacon Upgrade Works, LLC</span></div>
    <div class="rule rule--upper"></div>

    <address class="address" style="font-style:normal">
      4120 Alder Crest Road<br>
      Fairview, Oregon 97024<br>
      www.beaconworks.com
    </address>

    <div class="rule rule--lower"></div>
    <ul class="contacts">
      <li>
        <svg viewBox="0 0 12 12" aria-hidden="true"><path d="M1 3c0-1 1-2 2-2h6c1 0 2 1 2 2v1H8V3H4v1H1z M2 5h8l1 6H1z"/></svg>
        <span>555 214 7730</span>
      </li>
      <li>
        <svg viewBox="0 0 12 12" aria-hidden="true"><path d="M3 0h6v12H3z M4 1v8h4V1z"/></svg>
        <span>555 398 1264</span>
      </li>
      <li>
        <svg viewBox="0 0 12 12" aria-hidden="true"><path d="M3 0h6v4H3z M0 5h12v6H0z M2 7h3v1H2z"/></svg>
        <span>555 761 0485</span>
      </li>
      <li>
        <svg viewBox="0 0 12 12" aria-hidden="true"><path d="M0 2h12v1L6 7 0 3z M0 4.5l6 4 6-4V10H0z"/></svg>
        <span>hello@beaconworks.com</span>
      </li>
    </ul>
  </section>

</main>
</body>
</html>
```